Thornbury Building Company - Card Design

I am looking to use the logo designs that you already did for me to develop a business card. I would like the card to have a black background and be double sided. I want white and green logo and text. I have attached an inspiration photo of a look that I like. I would like to use the Vertical Logo attached to take up the full front side of the card. On the back where I have my name and information, I would like to have the horizontal logo or maybe even just the image of the 'A' and trees without the text. I am open, but I am looking for something clean and simple and I want the green to really pop! Additional files can be found under Design #: 58302946

Target Market(s)

Homeowners

Industry/Entity Type

Construction

Contact Information for Business Card

Name: Marcus Thornbury, Title: Project Manager, Phone: 555.274.8136, Email: thornburybuildingcompany@mailvesta.com, address: 487 Larkspur Ln, Felton, CA 95033, Lic# 2468317

Colors
00AB8E
00BBA5
67D7C9
C6EFE9
E9F9F6

Requirements
Nice to have
• I would like to see the logos that I have already got from ArtLoomHub, though I am open to new ones

```html
<!DOCTYPE html>
<html lang="en">
<head>
<meta charset="utf-8">
<title>Thornbury Building Company – Business Card</title>
<link rel="stylesheet" href="https://fonts.googleapis.com/css2?family=Montserrat:wght@400;500;700;800&display=swap">
<style>
  :root {
    --page-bg: #b9b9b9;
    --card-bg: #1c1c1c;
    --card-bg-alt: #202020;
    --brand-green: #6cbd45;
    --text-white: #ffffff;
    --text-muted: #e6e6e6;
  }
  * { box-sizing: border-box; margin: 0; padding: 0; }
  html, body {
    width: 1200px; height: 788px; overflow: hidden;
    background: var(--page-bg);
    font-family: "Montserrat", sans-serif;
  }
  .sheet {
    position: relative; width: 1200px; height: 788px;
    display: flex; align-items: center; justify-content: center; gap: 50px;
  }
  .card {
    position: relative; width: 525px; height: 300px;
    border-radius: 22px;
    background: var(--card-bg);
    box-shadow: 0 4px 0 var(--brand-green), 0 14px 24px rgba(0,0,0,.28);
    overflow: hidden;
  }

  /* Info side */
  .card--info { display: flex; align-items: center; }
  .info__brand {
    width: 190px; height: 100%;
    display: flex; flex-direction: column; align-items: center; justify-content: center; gap: 12px;
  }
  .brand-mark {
    width: 26px; height: 26px; background: var(--brand-green);
  }
  .brand-name {
    color: var(--brand-green); font-weight: 700; font-size: 15px;
    letter-spacing: .08em; text-transform: uppercase; text-align: center; line-height: 1.35;
  }
  .info__divider {
    width: 1px; height: 150px; background: var(--brand-green);
  }
  .info__details { padding-left: 28px; color: var(--text-white); }
  .person-name {
    color: var(--brand-green); font-weight: 800; font-size: 21px; letter-spacing: .02em;
    text-transform: uppercase;
  }
  .person-title { font-size: 12.5px; font-weight: 500; margin-top: 2px; }
  .licence { color: var(--brand-green); font-size: 12.5px; margin-top: 16px; }
  .address { font-size: 12.5px; margin-top: 2px; }
  .contact-list { list-style: none; margin-top: 16px; }
  .contact-list li {
    display: flex; align-items: center; gap: 8px; font-size: 12.5px; margin-top: 4px;
  }
  .contact-icon { width: 12px; height: 12px; fill: var(--brand-green); flex: none; }

  /* Brand side */
  .card--brand {
    background: linear-gradient(135deg, var(--card-bg-alt), var(--card-bg));
    display: flex; align-items: center; justify-content: center; gap: 16px;
  }
  .card--brand .brand-mark { width: 44px; height: 44px; }
  .card--brand .brand-name { font-size: 24px; text-align: left; line-height: 1.2; letter-spacing: .1em; }
</style>
</head>
<body>
<main class="sheet">
  <section class="card card--info" aria-label="Contact side">
    <div class="info__brand">
      <span class="brand-mark" aria-hidden="true"></span>
      <p class="brand-name">Thornbury<br>Building<br>Company</p>
    </div>
    <div class="info__divider"></div>
    <div class="info__details">
      <h1 class="person-name">Marcus Thornbury</h1>
      <p class="person-title">Project Manager</p>
      <p class="licence">Lic# 2468317</p>
      <p class="address">487 Larkspur Ln, Felton, CA 95033</p>
      <ul class="contact-list">
        <li>
          <svg class="contact-icon" viewBox="0 0 24 24" aria-hidden="true"><path d="M6.6 10.8a15 15 0 0 0 6.6 6.6l2.2-2.2a1 1 0 0 1 1-.25 11.4 11.4 0 0 0 3.6.57 1 1 0 0 1 1 1V20a1 1 0 0 1-1 1A17 17 0 0 1 3 4a1 1 0 0 1 1-1h3.5a1 1 0 0 1 1 1c0 1.25.2 2.45.57 3.6a1 1 0 0 1-.25 1z"/></svg>
          555.274.8136
        </li>
        <li>
          <svg class="contact-icon" viewBox="0 0 24 24" aria-hidden="true"><path d="M2 5h20v14H2z M2 5l10 8 10-8" /></svg>
          thornburybuildingcompany@mailvesta.com
        </li>
      </ul>
    </div>
  </section>

  <section class="card card--brand" aria-label="Brand side">
    <span class="brand-mark" aria-hidden="true"></span>
    <p class="brand-name">Thornbury<br>Building Company</p>
  </section>
</main>
</body>
</html>
```